Mobile version of Desktop site

I need a mobile version of my desktop site. Up until now we have been using a mobile translation service but there are too many drawbacks and bugs. So I need a mobile site designed to be used on an iPhone or android phone that is "Inspired by" our desktop site. I am going to setup two completely separate sites, served either as desktop or mobile.

I have attached an eps version of my logo.

Design this site as though the largest screen it will be viewed on is an iPhone 6 plus, but more likely it will be viewed on smaller screens.

Phone number as a button to click to call should be prominent.

Just need a basic attorney website that is clean and has the look and feel of the desktop site, but readable and usable on a smartphone.

Base your design off of an inner page like whats on this url:
Desktop url: https://www.brackenfieldlaw.com/mesa-verdan.html

Reason: I am extending the deadline to allow for implementation of feedback

Target Market(s)

everyone

Industry/Entity Type

Attorney

Number of Pages Required

1 page

Font styles to use
Sans Serif

Requirements
Must have
• Must be readable and usable on a smart phone, from a 5.5" iPhone 6 plus on down to the original iPhone. I'm looking for usability and readability.
Nice to have
• I would like to see logos shown at the top filling the width of the page if viewed in portrait mode with the phone number next, and it should be a complementing version of my desktop site.
Should not have
• I do not want to see a lot of small details that would be lost on a smartphone platform.

```html
<!DOCTYPE html>
<html lang="en">
<head>
<meta charset="utf-8">
<title>Brackenfield Attorneys – Mobile</title>
<link rel="stylesheet" href="https://fonts.googleapis.com/css2?family=Open+Sans:wght@400;600&display=swap">
<style>
  :root {
    --navy: #0e2f63;
    --navy-dark: #0a2148;
    --fold: #1d1d1d;
    --ink: #555555;
    --field-line: #b9b9b9;
    --card-line: #cfcfcf;
    --page: #eeeeee;
    --white: #ffffff;
    --sky-top: #8fb4d8;
    --sky-mid: #f3a56a;
    --sand: #c25a2c;
    --rule: #9aa4b4;
  }
  * { box-sizing: border-box; margin: 0; padding: 0; }
  html, body { width: 1200px; height: 1200px; overflow: hidden; background: var(--page); }
  body { font-family: "Open Sans", Arial, sans-serif; color: var(--ink); }

  .screen {
    position: absolute; left: 280px; top: 35px;
    width: 640px; height: 1130px;
    background: var(--white); overflow: hidden;
    box-shadow: 0 0 0 1px #d9d9d9;
  }

  .brand {
    position: absolute; left: 0; right: 0; top: 40px;
    text-align: center; color: var(--navy); font-weight: 600;
  }
  .brand__name { font-size: 58px; letter-spacing: 1px; line-height: 1; text-transform: uppercase; }
  .brand__sub { font-size: 20px; letter-spacing: 9px; text-transform: uppercase; margin-top: 6px; }

  .contact-row {
    position: absolute; left: 27px; right: 18px; top: 168px; height: 44px;
    display: flex; align-items: center;
  }
  .call-link { font-size: 32px; color: var(--navy); text-decoration: none; font-weight: 400; }
  .social { margin-left: auto; display: flex; gap: 26px; }
  .social__btn { display: flex; align-items: center; gap: 8px; }
  .social__label {
    height: 36px; padding: 0 10px; border-radius: 4px;
    display: flex; align-items: center; gap: 7px;
    font-size: 18px; font-weight: 600; color: var(--white); background: var(--navy);
  }
  .social__label i { width: 14px; height: 14px; background: var(--white); border-radius: 2px; display: block; }
  .social__label--light { background: var(--white); color: var(--ink); border: 1px solid var(--field-line); }
  .social__label--light i { background: #c9402f; }
  .social__count {
    height: 36px; min-width: 44px; padding: 0 8px; border: 1px solid var(--field-line);
    border-radius: 4px; font-size: 17px; display: flex; align-items: center; justify-content: center;
  }

  .nav-bar {
    position: absolute; left: 9px; right: 16px; top: 241px; height: 95px;
    background: var(--navy);
  }
  .nav-bar__toggle {
    position: absolute; right: 26px; top: 18px; width: 64px; height: 56px;
    border: 2px solid var(--white); border-radius: 8px;
    display: flex; align-items: center; justify-content: center;
  }

  .hero {
    position: absolute; left: 9px; right: 16px; top: 347px; height: 365px;
    background: linear-gradient(180deg, var(--sky-top) 0%, #d7c1b0 30%, var(--sky-mid) 52%, #3b2a2a 62%, var(--sand) 80%, #e59b5c 100%);
  }

  .enquiry {
    position: absolute; left: 98px; top: 745px; width: 438px; height: 420px;
    border: 1px solid var(--card-line); border-radius: 4px;
    background: linear-gradient(180deg, var(--white) 0%, #e9e9e9 100%);
  }
  .enquiry__ribbon {
    position: absolute; left: -25px; top: 25px; height: 46px; width: 375px;
    background: var(--navy);
    clip-path: polygon(0 0, 92% 0, 100% 50%, 92% 100%, 0 100%);
    color: var(--white); font-size: 21px; text-transform: uppercase;
    display: flex; align-items: center; padding-left: 48px;
  }
  .enquiry__fold { position: absolute; left: -25px; top: 71px; }
  .enquiry__title {
    position: absolute; left: 0; right: 0; top: 88px; text-align: center;
    color: var(--navy); font-size: 21px; font-weight: 600;
  }
  .enquiry__rule { position: absolute; left: 47px; width: 321px; top: 132px; border-top: 1px solid var(--rule); }
  .field { position: absolute; left: 13px; width: 395px; }
  .field__label { display: block; font-size: 17px; margin-bottom: 6px; }
  .field__input { display: block; width: 100%; height: 57px; border: 1px solid var(--field-line); background: var(--white); }
</style>
</head>
<body>
  <main class="screen">
    <header class="brand">
      <div class="brand__name">Brackenfield</div>
      <div class="brand__sub">Attorneys</div>
    </header>

    <div class="contact-row">
      <a class="call-link" href="tel:9495550142">(949) 555-0142</a>
      <div class="social">
        <div class="social__btn">
          <span class="social__label"><i></i>Like</span>
          <span class="social__count">6</span>
        </div>
        <div class="social__btn">
          <span class="social__label social__label--light"><i></i>Share</span>
          <span class="social__count">1.2k</span>
        </div>
      </div>
    </div>

    <nav class="nav-bar">
      <div class="nav-bar__toggle">
        <svg width="36" height="28" viewBox="0 0 36 28">
          <rect y="0" width="36" height="5" rx="2" fill="#fff"/>
          <rect y="11.5" width="36" height="5" rx="2" fill="#fff"/>
          <rect y="23" width="36" height="5" rx="2" fill="#fff"/>
        </svg>
      </div>
    </nav>

    <div class="hero" role="img" aria-label="Photo of a long ocean pier silhouetted against a sunset sky, reflected on wet sand"></div>

    <section class="enquiry">
      <div class="enquiry__ribbon">How can we help you</div>
      <svg class="enquiry__fold" width="25" height="22" viewBox="0 0 25 22"><polygon points="0,0 25,0 25,22" fill="var(--fold)"/></svg>
      <h2 class="enquiry__title">Talk To Us About Your Injury Now</h2>
      <div class="enquiry__rule"></div>
      <div class="field" style="top:160px"><span class="field__label">Name</span><span class="field__input"></span></div>
      <div class="field" style="top:264px"><span class="field__label">Email</span><span class="field__input"></span></div>
      <div class="field" style="top:368px"><span class="field__label">Phone</span></div>
    </section>
  </main>
</body>
</html>
```